BRN website video quote promotion tiles

We are promoting vehicle leasing by video, which contains several quotation examples imported from the video. We must re-vamp the quotation tiles, contact boxes, and contact form. The first tile is generated from the video, so this must be a separate project. We are looking for a welcoming, professional flow and leave color choices to design with an emphasis on communication prompts, and additional prompts in the design would be welcome.

Target Market(s)

Any Customer interaction from the tile quotes, contact, call, message,

Industry/Entity Type

vehicle leasing

Coding

Coded - Design and coding required

Number of Pages Required

1 page

Colors

Designer to choose colors to be used in the design.

Requirements
Must have
• emphasis on point of contact and visual impact on quote tile excluding main one
Should not have
• changes to the quote structure as these imported from video pricing no changes to main image as this template which can addressed as separate project

```html
<!DOCTYPE html>
<html lang="en">
<head>
<meta charset="utf-8">
<title>BRN Quote Tiles and Contact Form</title>
<link href="https://fonts.googleapis.com/css2?family=Lato:wght@400;700;900&display=swap" rel="stylesheet">
<style>
  :root {
    --green: #92c050;
    --orange: #e07f32;
    --yellow: #e9bd3f;
    --red: #e0101a;
    --ink: #1d1d1d;
    --tile: #f2f0f0;
    --tile-tint: #e8ebe2;
    --field: #e3e3e3;
    --white: #ffffff;
  }
  * { box-sizing: border-box; margin: 0; padding: 0; }
  html, body { width: 1200px; height: 777px; overflow: hidden; background: var(--white); font-family: "Lato", sans-serif; color: var(--ink); }
  .canvas { position: relative; width: 1200px; height: 777px; }

  .form-frame { position: absolute; left: 396px; top: 47px; width: 408px; height: 391px; background: var(--white); box-shadow: 0 1px 5px rgba(0,0,0,.18); }
  .form-panel { position: absolute; left: 19px; top: 26px; width: 370px; height: 340px; border-radius: 12px;
    background: radial-gradient(ellipse at 30% 10%, #ececec 0%, #f7f7f7 45%, #f4f4f4 100%); }
  .form-title { position: absolute; top: 17px; width: 100%; text-align: center; font-size: 17px; font-weight: 700; }
  .field-label { position: absolute; left: 27px; font-size: 8.5px; font-weight: 700; }
  .field { position: absolute; left: 27px; width: 317px; height: 28px; background: var(--field); border-radius: 3px; border: none; }
  .field.message { height: 61px; }
  .submit { position: absolute; left: 144px; top: 294px; width: 84px; height: 25px; background: var(--green); color: var(--white); border: none; border-radius: 2px; font: 700 8.5px "Lato", sans-serif; }

  .quotes-band { position: absolute; left: 46px; top: 482px; width: 1107px; height: 247px; background: var(--white); box-shadow: 0 1px 5px rgba(0,0,0,.18); }
  .quote-tile { position: absolute; top: 31px; width: 325px; height: 186px; background: var(--tile); border-radius: 14px; }
  .tile-title { position: absolute; font-size: 22px; font-weight: 900; white-space: nowrap; }
  .tile-terms { position: absolute; font-size: 15.5px; line-height: 20px; }
  .tile-note { position: absolute; font-size: 12.5px; line-height: 17px; }
  .btn { position: absolute; height: 28px; border-radius: 2px; color: var(--white); font-size: 13px; display: flex; align-items: center; justify-content: center; }
  .btn-contact { width: 100px; background: var(--orange); }
  .btn-chat { width: 56px; background: var(--green); font-size: 10px; font-weight: 700; }
  .btn-price { width: 100px; background: var(--yellow); }
  .vat-tag { position: absolute; left: 29px; top: 24px; width: 42px; height: 13px; background: var(--green); color: var(--white); font-size: 5.5px; font-weight: 700; display: flex; align-items: center; justify-content: center; }
  .centered { left: 0; width: 100%; text-align: center; }
  .tile-highlight { position: absolute; left: 18px; top: 11px; width: 292px; height: 105px; background: var(--tile-tint); border-radius: 4px; }
</style>
</head>
<body>
<div class="canvas">

  <section class="form-frame">
    <form class="form-panel">
      <h1 class="form-title">Please Submit Your Contact Details</h1>
      <label class="field-label" style="top:59px">Your Name</label>
      <input class="field" style="top:68px" type="text">
      <label class="field-label" style="top:109px">Email</label>
      <input class="field" style="top:118px" type="email">
      <label class="field-label" style="top:160px">Contact Number</label>
      <input class="field" style="top:169px" type="tel">
      <label class="field-label" style="top:210px">Message</label>
      <textarea class="field message" style="top:219px"></textarea>
      <button class="submit" type="submit">Submit</button>
    </form>
  </section>

  <section class="quotes-band">
    <article class="quote-tile" style="left:34px">
      <h2 class="tile-title centered" style="top:20px;color:var(--green)">Contract Hire</h2>
      <p class="tile-terms centered" style="top:55px">3&nbsp; Years, 9+35, 10K Miles Annually</p>
      <p class="tile-note centered" style="top:85px;color:var(--red)">Not Maintained</p>
      <div class="btn btn-contact" style="left:20px;top:124px">Contact Us</div>
      <div class="btn btn-chat" style="left:135px;top:124px">ChatLine</div>
      <div class="btn btn-price" style="left:206px;top:124px">£247.33<span class="vat-tag">PLUS VAT</span></div>
    </article>

    <article class="quote-tile" style="left:391px">
      <h2 class="tile-title" style="left:22px;top:32px;color:var(--yellow)">Contract Hire</h2>
      <p class="tile-terms" style="left:23px;top:67px;width:170px">3&nbsp; Years, 9+35, 10K Miles Annually</p>
      <p class="tile-note" style="left:23px;top:117px;width:150px;color:var(--orange)">Complete Servicing and Maintenance Included</p>
      <div class="btn btn-price" style="left:202px;top:23px">£247.33<span class="vat-tag">PLUS VAT</span></div>
      <div class="btn btn-chat" style="left:224px;top:83px">ChatLine</div>
      <div class="btn btn-contact" style="left:202px;top:135px">Contact Us</div>
    </article>

    <article class="quote-tile" style="left:749px">
      <div class="tile-highlight"></div>
      <h2 class="tile-title centered" style="top:22px;color:var(--orange)">Contract Hire</h2>
      <p class="tile-terms centered" style="top:52px;font-size:14.5px">3&nbsp; Years, 9+35, 10K Miles Annually</p>
      <p class="tile-note centered" style="top:73px;color:var(--green)">Complete Servicing and Maintenance Included</p>
      <div class="btn btn-price" style="left:46px;top:101px">£247.33<span class="vat-tag">PLUS VAT</span></div>
      <div class="btn btn-contact" style="left:178px;top:101px">Contact Us</div>
      <div class="btn btn-chat" style="left:135px;top:142px">ChatLine</div>
    </article>
  </section>

</div>
</body>
</html>
```